Residential & commercial landscaping company

Updated business cards for commercial and landscaping company. We would like to keep out logo, but just need a more updated business card.

```html
<!DOCTYPE html>
<html lang="en">
<head>
<meta charset="UTF-8">
<title>Verdant Ridge – Business Cards</title>
<link href="https://fonts.googleapis.com/css2?family=Arimo:wght@400;700&display=swap" rel="stylesheet">
<style>
  :root {
    --backdrop: #141414;
    --card: #ffffff;
    --brand-green: #119a3c;
    --rule-green: #4cc43f;
    --dark-green: #0d7a35;
    --ink: #111111;
    --text-grey: #4a4a4a;
  }
  * { box-sizing: border-box; margin: 0; padding: 0; }
  html, body {
    width: 1200px; height: 820px; overflow: hidden;
    background: var(--backdrop);
    font-family: "Arimo", Arial, sans-serif;
  }
  .sheet {
    position: relative; width: 1200px; height: 820px;
    display: flex; align-items: center; justify-content: center; gap: 60px;
  }
  .card {
    position: relative;
    width: 525px; height: 300px;
    background: var(--card);
    border-bottom: 4px solid var(--brand-green);
    border-right: 2px solid var(--brand-green);
    box-shadow: 0 18px 40px rgba(0,0,0,.6);
  }
  .card--back { margin-top: -140px; }
  .card--front { margin-top: 140px; }

  .wordmark {
    position: absolute;
    display: flex; align-items: center; gap: 10px;
    color: var(--ink); font-weight: 700; letter-spacing: -1px; white-space: nowrap;
  }
  .wordmark__square { display: block; background: var(--dark-green); }
  .card--front .wordmark { right: 40px; top: 78px; font-size: 38px; }
  .card--front .wordmark__square { width: 26px; height: 26px; }
  .card--back .wordmark { left: 50%; top: 50%; transform: translate(-50%, -50%); font-size: 50px; }
  .card--back .wordmark__square { width: 34px; height: 34px; }

  .rule {
    position: absolute; left: 232px; right: 24px; top: 152px;
    height: 2px; background: var(--rule-green);
  }
  .contact { position: absolute; left: 32px; top: 130px; }
  .contact__name { color: var(--brand-green); font-weight: 700; font-size: 22px; line-height: 1.1; }
  .contact__title { color: var(--text-grey); font-size: 14px; margin-top: 3px; }
  .contact__list { list-style: none; margin-top: 14px; }
  .contact__item {
    display: flex; align-items: center; gap: 10px;
    color: var(--text-grey); font-size: 14.5px; line-height: 23px;
  }
  .contact__item svg { width: 15px; height: 15px; flex: none; fill: var(--brand-green); }
  .contact__web { color: var(--brand-green); }
</style>
</head>
<body>
<main class="sheet">
  <section class="card card--front" aria-label="Business card front">
    <div class="wordmark"><span class="wordmark__square"></span>Verdant Ridge</div>
    <div class="rule"></div>
    <div class="contact">
      <p class="contact__name">Daniel Harrow</p>
      <p class="contact__title">Jr. Project Manager</p>
      <ul class="contact__list">
        <li class="contact__item">
          <svg viewBox="0 0 16 16" aria-hidden="true"><path d="M3.5 1.5l2.5 3-1.5 1.5c.8 2 2.5 3.7 4.5 4.5L10.5 9l3 2.5-1.5 2.5C7 14 2 9 2 3.5z"/></svg>
          555-210-4480 ext.312
        </li>
        <li class="contact__item">
          <svg viewBox="0 0 16 16" aria-hidden="true"><rect x="4" y="1" width="8" height="4"/><rect x="1" y="6" width="14" height="6" rx="1"/><rect x="4" y="10" width="8" height="5" fill="#fff" stroke="#119a3c" stroke-width="1.4"/></svg>
          555-730-9164
        </li>
        <li class="contact__item">
          <svg viewBox="0 0 16 16" aria-hidden="true"><rect x="1" y="3" width="14" height="10"/><path d="M1.5 3.5L8 9l6.5-5.5" fill="none" stroke="#fff" stroke-width="1.4"/></svg>
          dan@VerdantRidgeGrounds.com
        </li>
        <li class="contact__item">
          <svg viewBox="0 0 16 16" aria-hidden="true"><circle cx="8" cy="8" r="7"/><g fill="none" stroke="#fff" stroke-width="1"><ellipse cx="8" cy="8" rx="3" ry="7"/><path d="M1 8h14M2.5 4.5h11M2.5 11.5h11"/></g></svg>
          <span>www.<span class="contact__web">VerdantRidgeGrounds</span>.com</span>
        </li>
      </ul>
    </div>
  </section>

  <section class="card card--back" aria-label="Business card back">
    <div class="wordmark"><span class="wordmark__square"></span>Verdant Ridge</div>
  </section>
</main>
</body>
</html>
```